Business Card Design for ReaL ESTATE AGENT

New Business Cards for a real estate agent in Jacksonville, FL. My specialty is urban core, historic districts but sell through out the city. Company Name is Ninth and Crest Realty a division of the Dunholt Companies. The card needs to convey an essence of professionalism, knowledge and success.

Target Market(s)

Home buyers and Sellers

Industry/Entity Type

Real Estate

Contact Information for Business Card

Double sided

Font styles to use
Sans Serif

Requirements
Must have
• My logs and photo (provided). My contact information as follows:
• Owen Talbrick
• Cell 904-555-0183
• Office 904-555-0147
• Email owentalbrick@mailbrook.example
Nice to have
• Tag Line - Exceptional Effort. Proven Results.

```html
<!DOCTYPE html>
<html lang="en">
<head>
<meta charset="utf-8">
<title>Ninth and Crest Realty – Business Card</title>
<link href="https://fonts.googleapis.com/css2?family=Source+Sans+3:wght@400;600;700&display=swap" rel="stylesheet">
<style>
  :root {
    --backdrop-top: #2a2a2a;
    --backdrop-bottom: #050505;
    --card-white: #ffffff;
    --brand-green: #22634a;
    --name-green: #1d5a3f;
    --text-dark: #2b2b2b;
    --photo-light: #e9e7e4;
    --photo-mid: #9a8f86;
    --photo-dark: #2f2f33;
  }
  * { box-sizing: border-box; margin: 0; padding: 0; }
  html, body {
    width: 1200px;
    height: 900px;
    overflow: hidden;
  }
  body {
    position: relative;
    background: linear-gradient(180deg, var(--backdrop-top) 0%, #161616 55%, var(--backdrop-bottom) 100%);
    font-family: "Source Sans 3", sans-serif;
  }
  .card {
    position: absolute;
    top: 306px;
    width: 440px;
    height: 271px;
    background: var(--card-white);
    border-radius: 10px;
    overflow: hidden;
  }
  .card--front { left: 149px; }
  .card--back { left: 608px; }

  .band {
    position: absolute;
    left: 0;
    width: 100%;
    background: var(--brand-green);
  }
  .band--top { top: 0; height: 36px; }
  .band--bottom { bottom: 0; height: 28px; }

  .portrait {
    position: absolute;
    left: 0;
    top: 36px;
    width: 173px;
    height: 207px;
    background: linear-gradient(180deg, var(--photo-light) 0%, var(--photo-light) 45%, var(--photo-mid) 62%, var(--photo-dark) 82%);
  }

  .agent {
    position: absolute;
    left: 228px;
    top: 88px;
    color: var(--text-dark);
    white-space: nowrap;
  }
  .agent__name {
    font-size: 18.5px;
    font-weight: 600;
    color: var(--name-green);
    line-height: 1.1;
    letter-spacing: 0.1px;
  }
  .agent__title {
    font-size: 14px;
    margin-top: 3px;
    line-height: 1.1;
  }
  .contact {
    list-style: none;
    margin-top: 18px;
    font-size: 12.5px;
    line-height: 18px;
  }
  .contact__item {
    display: flex;
    align-items: center;
    gap: 7px;
  }
  .contact__icon {
    width: 11px;
    height: 11px;
    fill: var(--name-green);
    flex: none;
  }

  .brand {
    position: absolute;
    inset: 0;
    display: flex;
    flex-direction: column;
    align-items: center;
    justify-content: center;
    gap: 14px;
  }
  .brand__mark {
    width: 46px;
    height: 46px;
    border: 4px solid var(--brand-green);
  }
  .brand__name {
    font-size: 27px;
    font-weight: 700;
    color: var(--brand-green);
    text-align: center;
    line-height: 1.15;
    letter-spacing: 0.5px;
  }
</style>
</head>
<body>
  <section class="card card--front" aria-label="Card front">
    <div class="band band--top"></div>
    <div class="portrait" role="img" aria-label="Portrait photo of the agent in a dark suit and red tie"></div>
    <div class="agent">
      <h1 class="agent__name">Owen Talbrick</h1>
      <p class="agent__title">Managing Director</p>
      <ul class="contact">
        <li class="contact__item">
          <svg class="contact__icon" viewBox="0 0 12 12" aria-hidden="true">
            <path d="M1 4.2C1 2.6 3.5 1.8 6 1.8s5 .8 5 2.4v.9H8.6v-1H3.4v1H1z"/>
            <path d="M3 5.6h6l1.6 4.6H1.4z"/>
          </svg>
          <span>Cell 904-555-0183</span>
        </li>
        <li class="contact__item">
          <svg class="contact__icon" viewBox="0 0 12 12" aria-hidden="true">
            <path d="M1 4.2C1 2.6 3.5 1.8 6 1.8s5 .8 5 2.4v.9H8.6v-1H3.4v1H1z"/>
            <path d="M3 5.6h6l1.6 4.6H1.4z"/>
          </svg>
          <span>Office 904-555-0147</span>
        </li>
        <li class="contact__item">
          <svg class="contact__icon" viewBox="0 0 12 12" aria-hidden="true">
            <path d="M1 3h10v6.5H1z M1.6 3.4 6 6.9l4.4-3.5" stroke="#fff" stroke-width="0.9"/>
          </svg>
          <span>owentalbrick@mailbrook.example</span>
        </li>
      </ul>
    </div>
    <div class="band band--bottom"></div>
  </section>

  <section class="card card--back" aria-label="Card back">
    <div class="brand">
      <div class="brand__mark" aria-hidden="true"></div>
      <p class="brand__name">Ninth and Crest<br>Realty</p>
    </div>
  </section>
</body>
</html>
```